Digital Marketing Website Redesign, modern, fresh, dynamic

Hi there, we would like to freshen up our website and create a new dynamic look. We are a digital marketing agency who specialise in digital transformation in the form of creating websites for appointment bookings. Our clients are service businesses such as hairdressers, dentists and doctors who's patients need to book appointments with them.

Our company name is Tallomex with the point being we can help increase your revenue curve by increasing your appointment bookings.

Our services include building the website, creating campaigns to drive traffic, increasing conversions and monitoring and reporting.

We are playing with a tagline of 'Step into your Digital Transformation' as we have a 5 step journey that customers can take with us getting them from zero to full appointment bookings.

Our current website is www.tallomex-sample.com

You can see a draft design that I mocked up on Canva here https://www.draftboard-sample.com/design/QXB82LmpR7T/KpoW39dnFsYbZet_wqe_OPa/edit?utm_content=QXB82LmpR7T&utm_campaign=designshare&utm_medium=link2&utm_source=sharebutton

Also attached some other homepage ideas. In regard to photos we are open to ideas.

Please let if you need any more information to provide us with an initial design. Thanks million and I look forward to receiving fantastic designs :)

Marian Dobbs
Tallomex

Target Market(s)

Appointment based businesses such as hairdressers, dentists, doctors

Industry/Entity Type

Marketing and Digital

Coding

Coded - Design and coding required

Number of Pages Required

1 page

Colors
0094D4
00A9DD
6FCCEA
C7EBF8
E9F6FB

Requirements
Must have
• Appointment booking CTA
Nice to have
• A website we like https://www.fergalwhitty-sample.ie

```html
<!DOCTYPE html>
<html lang="en">
<head>
<meta charset="utf-8">
<title>Tallomex — Digital Transformation Consultancy</title>
<link rel="stylesheet" href="https://fonts.googleapis.com/css2?family=Manrope:wght@400;500;600;700;800&family=Inter:wght@400;500;600&display=swap">
<style>
:root{
  --brand:#0094D4;
  --brand-2:#00A9DD;
  --brand-soft:#6FCCEA;
  --brand-pale:#C7EBF8;
  --brand-mist:#E9F6FB;
  --brand-deep:#006f9f;
  --navy:#1d2233;
  --ink:#2a2d3a;
  --muted:#8a8e99;
  --hero-a:#0a4f9c;
  --hero-b:#0094D4;
  --chart:#1c3a63;
  --white:#ffffff;
  --line:#e3e4e8;
}
*{box-sizing:border-box;margin:0;padding:0}
html,body{width:1200px;height:5236px;overflow:hidden}
body{font-family:"Inter",sans-serif;color:var(--ink);background:var(--white);position:relative}
h1,h2,h3,h4{font-family:"Manrope",sans-serif}
section,header,footer{position:relative;width:1200px}
.abs{position:absolute}
.eyebrow{font-size:12px;letter-spacing:2px;font-weight:600;color:var(--brand);text-transform:uppercase}
.btn{display:flex;align-items:center;justify-content:center;background:var(--brand);color:#fff;font-size:14px;font-weight:500;text-decoration:none}

/* nav */
.site-nav{height:71px;background:#fff}
.logo{font-family:"Manrope",sans-serif;font-weight:800;color:var(--navy);display:flex;align-items:center;gap:6px}
.logo i{display:block;border-radius:50%;background:var(--brand)}
.site-nav .logo{left:65px;top:20px;font-size:22px}
.site-nav .logo i{width:10px;height:10px}
.nav-links a{position:absolute;top:26px;font-size:14px;font-weight:500;color:var(--navy);text-decoration:none}
.nav-links a.active{color:var(--brand)}

/* hero */
.hero{height:787px;color:#fff}
.hero-visual{position:absolute;inset:0;background:radial-gradient(ellipse at 50% 60%,var(--brand-soft) 0%,var(--hero-b) 38%,var(--hero-a) 85%)}
.hero .badge{left:50%;transform:translateX(-50%);top:177px;background:var(--brand-pale);color:var(--navy);font-size:12px;letter-spacing:1.5px;font-weight:600;padding:7px 20px;white-space:nowrap}
.hero h1{top:230px;width:100%;text-align:center;font-size:56px;line-height:57px;font-weight:700;letter-spacing:-1px}
.hero p{top:366px;left:280px;width:640px;text-align:center;font-size:15px;line-height:20px}
.hero .btn{left:460px;top:503px;width:280px;height:48px;font-size:15px;background:var(--brand-pale);color:var(--navy);font-weight:600}
.stats{left:0;top:651px;width:1200px;height:136px;background:rgba(6,34,80,.55);display:flex}
.stat{flex:1;text-align:center;padding-top:16px}
.stat b{display:block;font-family:"Manrope",sans-serif;font-size:64px;line-height:72px;font-weight:700;color:var(--brand-soft)}
.stat span{font-size:18px}

/* about */
.about{height:820px}
.about .eyebrow{left:47px;top:142px}
.about h2{left:47px;top:176px;font-size:38px;line-height:48px;font-weight:700;color:var(--navy)}
.about .lead{left:47px;top:290px;width:380px;font-size:14px;line-height:23px;color:var(--muted)}
.feature{left:47px;width:390px}
.feature svg{position:absolute;left:0;top:2px}
.feature h4{margin-left:51px;font-size:17px;font-weight:600;color:var(--navy)}
.feature p{margin-left:51px;margin-top:10px;font-size:14px;line-height:23px;color:var(--muted)}
.about-photo{left:505px;top:120px;width:635px;height:562px;background:linear-gradient(135deg,#dfe4e8,#bcc5cc 55%,#8e99a2)}

/* services */
.services{height:522px;background:var(--brand-mist)}
.services .eyebrow{width:100%;text-align:center;top:46px}
.services h2{width:100%;text-align:center;top:80px;font-size:38px;font-weight:700;color:var(--navy)}
.svc{top:179px;width:262px;height:285px;background:#fff;box-shadow:0 10px 30px rgba(0,0,0,.07);padding:0 30px}
.svc svg{margin-top:46px}
.svc h3{margin-top:14px;font-size:22px;line-height:31px;font-weight:600;color:var(--navy)}
.svc p{margin-top:10px;font-size:14px;line-height:22px;color:var(--muted)}

/* heights */
.heights{height:312px}
.heights h2{left:75px;top:54px;font-size:40px;line-height:46px;font-weight:700;color:var(--navy);letter-spacing:-1px}
.heights .rule{left:75px;top:168px;width:48px;height:3px;background:var(--brand)}
.heights p{left:645px;top:56px;width:450px;font-size:14px;line-height:23px;color:var(--muted)}
.heights .btn{left:645px;top:176px;width:140px;height:32px;font-size:13px}

/* case studies */
.cases{height:508px}
.case{top:0;width:352px;height:417px;background:#fff;box-shadow:0 6px 20px rgba(0,0,0,.06)}
.case-top{display:flex;height:210px}
.case-stat{width:150px;background:var(--brand-mist);padding:12px 14px;position:relative}
.case-stat b{font-family:"Manrope",sans-serif;font-size:34px;font-weight:800;color:var(--brand-deep);display:block;line-height:38px}
.case-stat small{display:block;font-size:8px;font-weight:700;line-height:10px;color:var(--navy);margin-top:4px;text-transform:uppercase}
.case-stat .client{position:absolute;left:14px;bottom:10px;font-family:"Manrope",sans-serif;font-size:14px;font-weight:700;color:var(--navy)}
.case-chart{flex:1;background:var(--chart)}
.case h3{margin:32px 0 0 30px;font-size:22px;line-height:30px;font-weight:500;color:var(--brand)}
.case .name{margin:12px 0 0 30px;font-size:14px;color:var(--ink)}
.case .btn{position:absolute;left:0;bottom:0;width:100%;height:45px}

/* pricing */
.pricing{height:946px;background:var(--brand-mist)}
.pricing .eyebrow{width:100%;text-align:center;top:60px}
.pricing h2{width:100%;text-align:center;top:96px;font-size:40px;font-weight:700;color:var(--navy);letter-spacing:-1px}
.pricing .sub{width:100%;text-align:center;top:164px;font-size:14px;color:var(--muted)}
.plan{top:224px;width:350px;height:655px;text-align:center;background:#fff;box-shadow:0 6px 24px rgba(0,0,0,.05)}
.plan .ico{width:56px;height:56px;margin:31px auto 0;background:var(--brand);display:flex;align-items:center;justify-content:center}
.plan h3{margin-top:24px;font-size:22px;font-weight:500;color:var(--navy)}
.plan .desc{margin:10px auto 0;width:290px;font-size:14px;line-height:22px;color:var(--muted)}
.plan .price{margin-top:26px;font-family:"Manrope",sans-serif;font-size:54px;font-weight:700;color:var(--navy);position:relative;display:inline-block}
.plan .price sup{position:absolute;left:100%;top:8px;margin-left:8px;font-size:13px;font-weight:500;white-space:nowrap}
.plan ul{list-style:none;margin-top:26px}
.plan li{font-size:14px;height:35.5px;color:var(--muted)}
.plan .btn{margin:24px auto 0;width:290px;height:41px}
.plan .note{margin:20px auto 0;width:290px;font-size:11px;line-height:18px;color:var(--muted)}
.plan.featured{background:var(--brand)}
.plan.featured h3,.plan.featured .desc,.plan.featured .price,.plan.featured li,.plan.featured .note{color:#fff}
.plan.featured .ico{background:#fff}
.plan.featured .btn{background:#fff;color:var(--navy)}
.plan.alt{background:#f3f9fc}

/* contact */
.contact{height:625px}
.contact-panel{left:43px;top:112px;width:423px;height:513px;color:#fff}
.contact-visual{position:absolute;inset:0;background:linear-gradient(160deg,var(--brand-soft),var(--brand-2) 55%,var(--brand))}
.contact-panel .eyebrow{color:var(--brand-mist);left:59px;top:106px}
.contact-panel h2{left:59px;top:134px;font-size:36px;line-height:44px;font-weight:700}
.contact-panel p{left:59px;top:250px;width:310px;font-size:14px;line-height:20px}
.contact-panel .mail{left:59px;top:342px;font-size:22px}
.contact-panel .tel{left:59px;top:391px;font-size:22px}
.form-card{left:498px;top:112px;width:645px;height:513px;background:#fff;box-shadow:0 10px 40px rgba(0,0,0,.08)}
.form-card h2{left:61px;top:58px;font-size:34px;font-weight:700;color:var(--navy);letter-spacing:-.5px}
.form-card .intro{left:61px;top:118px;width:510px;font-size:13px;line-height:20px;color:var(--muted)}
.form-card label{position:absolute;font-size:13px;font-weight:600;color:var(--navy)}
.field{position:absolute;border:1px solid var(--line);background:#fff;font-size:13px;color:#9a9da6;padding:12px 16px}
.form-card .btn{left:61px;top:377px;width:525px;height:41px;font-size:13px}

/* newsletter */
.newsletter{height:177px;margin-top:114px;background:linear-gradient(90deg,var(--brand-2),var(--brand) 60%,var(--brand-deep))}
.newsletter h2{left:45px;top:54px;font-size:31px;line-height:39px;font-weight:700;color:#fff;letter-spacing:-.5px}
.newsletter .field{left:838px;top:40px;width:322px;height:43px;border:none}
.newsletter .signup{left:838px;top:95px;width:322px;height:41px;background:var(--navy);color:#fff;font-size:14px;display:flex;align-items:center;justify-content:center;gap:6px}

/* footer */
.site-footer{height:354px;background:#fff}
.site-footer .logo{left:87px;top:126px;font-size:50px}
.site-footer .logo i{width:16px;height:16px}
.fcol{top:75px}
.fcol h4{font-size:22px;font-weight:600;color:var(--navy);margin-bottom:14px}
.fcol a{display:block;font-size:13px;line-height:27.5px;color:var(--muted);text-decoration:none}
.fcol p{font-size:14px;line-height:24px;color:var(--muted)}
.socials{display:flex;gap:10px;margin-top:20px;margin-left:24px}
.socials span{width:22px;height:22px;background:var(--brand);display:block}
.legal{top:330px;font-size:11px;color:var(--muted)}
</style>
</head>
<body>

<header class="site-nav">
  <div class="abs logo"><i></i>Tallomex</div>
  <nav class="nav-links">
    <a class="active" style="left:352px">Home</a>
    <a style="left:427px">About</a>
    <a style="left:504px">Services</a>
    <a style="left:600px">Case Studies</a>
    <a style="left:728px">Pricing</a>
    <a style="left:812px">Contact</a>
  </nav>
  <a class="abs btn" style="left:1005px;top:16px;width:138px;height:41px">Book Now</a>
</header>

<section class="hero">
  <div class="hero-visual" role="img" aria-label="Person walking through a glowing blue digital corridor of circuit lines"></div>
  <div class="abs badge">STEP INTO YOUR DIGITAL TRANSFORMATION</div>
  <h1 class="abs">Digital Transformation<br>Consultancy</h1>
  <p class="abs">Let us help transform your business digitally and let your team, customers &amp; partners engage online. Tallomex simplifies digital integration of your intranet, extranet and internet communities. Specialists in boutique ecommerce and online appointment sales.</p>
  <a class="abs btn">Book an Appointment</a>
  <div class="abs stats">
    <div class="stat"><b>20+</b><span>Years Of Experience</span></div>
    <div class="stat"><b>250+</b><span>Projects Done</span></div>
    <div class="stat"><b>50%</b><span>Customer Satisfaction</span></div>
  </div>
</section>

<section class="about">
  <div class="abs eyebrow">About us</div>
  <h2 class="abs">Tallomex<br>Management</h2>
  <p class="abs lead">Tallomex's management team headed up by Conor Ashby and Declan Furlow provide 40+ years of collective experience in internet marketing and software application delivery.</p>
  <div class="abs feature" style="top:430px">
    <svg width="36" height="36" viewBox="0 0 36 36"><circle cx="18" cy="18" r="16" fill="none" stroke="#0094D4" stroke-width="2"/><path d="M11 18l5 5 9-10" fill="none" stroke="#0094D4" stroke-width="2.2"/></svg>
    <h4>Certified Expert Team</h4>
    <p>Porta semper magna elementum vel auctor tempus pulvinar dignissim rutrum egestas si</p>
  </div>
  <div class="abs feature" style="top:525px">
    <svg width="36" height="36" viewBox="0 0 36 36"><circle cx="18" cy="18" r="16" fill="none" stroke="#0094D4" stroke-width="2"/><path d="M11 18l5 5 9-10" fill="none" stroke="#0094D4" stroke-width="2.2"/></svg>
    <h4>Smart Solutions</h4>
    <p>Porta semper magna elementum vel auctor tempus pulvinar dignissim rutrum egestas si</p>
  </div>
  <div class="abs feature" style="top:620px">
    <svg width="36" height="36" viewBox="0 0 36 36"><circle cx="18" cy="18" r="16" fill="none" stroke="#0094D4" stroke-width="2"/><path d="M11 18l5 5 9-10" fill="none" stroke="#0094D4" stroke-width="2.2"/></svg>
    <h4>24/7 Premium Support</h4>
    <p>Porta semper magna elementum vel auctor tempus pulvinar dignissim rutrum egestas si</p>
  </div>
  <div class="abs about-photo" role="img" aria-label="Business team meeting around an office table with laptops and a flip chart"></div>
</section>

<section class="services">
  <div class="abs eyebrow">What we offer</div>
  <h2 class="abs">Our Services</h2>
  <article class="abs svc" style="left:47px">
    <svg width="40" height="34" viewBox="0 0 40 34" fill="none" stroke="#0094D4" stroke-width="2"><rect x="2" y="4" width="36" height="26"/><path d="M9 24V16M15 24V11M21 24V14M27 24V9"/></svg>
    <h3>Market Research</h3>
    <p>Ex suspendisse semper si sociosqu platea accumsan adipiscing diam maecenas consectetur at</p>
  </article>
  <article class="abs svc" style="left:328px">
    <svg width="40" height="34" viewBox="0 0 40 34" fill="none" stroke="#0094D4" stroke-width="2"><path d="M4 13h6l12-8v24l-12-8H4z"/><path d="M28 11c3 3 3 9 0 12M32 7c5 5 5 15 0 20"/></svg>
    <h3>Creative Campaigns</h3>
    <p>Ex suspendisse semper si sociosqu platea accumsan adipiscing diam maecenas consectetur at</p>
  </article>
  <article class="abs svc" style="left:610px">
    <svg width="40" height="34" viewBox="0 0 40 34" fill="none" stroke="#0094D4" stroke-width="2"><circle cx="20" cy="8" r="5"/><circle cx="9" cy="26" r="5"/><circle cx="31" cy="26" r="5"/><path d="M17 12l-5 9M23 12l5 9M14 26h12"/></svg>
    <h3>Lead<br>Management</h3>
    <p>Ex suspendisse semper si sociosqu platea accumsan adipiscing diam maecenas consectetur at</p>
  </article>
  <article class="abs svc" style="left:891px">
    <svg width="40" height="34" viewBox="0 0 40 34" fill="none" stroke="#0094D4" stroke-width="2"><rect x="4" y="4" width="26" height="18"/><path d="M1 27h32"/><rect x="30" y="12" width="8" height="16"/></svg>
    <h3>Online Bookings</h3>
    <p>Ex suspendisse semper si sociosqu platea accumsan adipiscing diam maecenas consectetur at</p>
  </article>
</section>

<section class="heights">
  <h2 class="abs">We bring your business to<br>new heights.</h2>
  <div class="abs rule"></div>
  <p class="abs">Lobortis tortor vestibulum class sagittis fermentum arcu pede aliquet in morbi mus. Ac metus sem luctus facilisi sapien et praesent erat tellus penatibus feugiat. Duis augue himenaeos rhoncus ac laoreet.</p>
  <a class="abs btn">Discover more</a>
</section>

<section class="cases">
  <article class="abs case" style="left:55px">
    <div class="case-top">
      <div class="case-stat"><b>1050%</b><small>Increase in customer base using free sampler</small><span class="client">Brindlewood</span></div>
      <svg class="case-chart" viewBox="0 0 202 210" preserveAspectRatio="none"><g stroke="#3d5a86" stroke-width="1"><path d="M20 10V195H198"/><path d="M20 60H198M20 110H198M20 160H198"/></g><polyline points="30,185 70,170 110,140 150,115 190,20" fill="none" stroke="#6FCCEA" stroke-width="2"/></svg>
    </div>
    <h3>ONLINE MARKETING<br>SERVICE</h3>
    <div class="name">Brindlewood</div>
    <a class="btn">Discover more</a>
  </article>
  <article class="abs case" style="left:425px">
    <div class="case-top">
      <div class="case-stat"><b style="font-size:18px;line-height:26px">625% MORE</b><small>New patients every month</small><span class="client">Brightmolar</span></div>
      <svg class="case-chart" viewBox="0 0 202 210" preserveAspectRatio="none"><g stroke="#3d5a86" stroke-width="1"><path d="M20 10V195H198"/><path d="M20 60H198M20 110H198M20 160H198"/></g><polyline points="30,150 65,185 100,175 140,110 170,70 190,15" fill="none" stroke="#6FCCEA" stroke-width="2"/></svg>
    </div>
    <h3>ONLINE MARKETING<br>SERVICE</h3>
    <div class="name">Brightmolar</div>
    <a class="btn">Discover more</a>
  </article>
  <article class="abs case" style="left:795px">
    <div class="case-top">
      <div class="case-stat"><b>100+</b><small>Appointment reservations after covid-19 lockdown</small><span class="client">Cutwell &amp; Co</span></div>
      <svg class="case-chart" viewBox="0 0 202 210" preserveAspectRatio="none"><g stroke="#3d5a86" stroke-width="1"><path d="M20 10V195H198"/><path d="M20 60H198M20 110H198M20 160H198"/></g><polyline points="30,190 120,190 150,140 190,15" fill="none" stroke="#6FCCEA" stroke-width="2"/></svg>
    </div>
    <h3>FREE ONLINE<br>CONSULTATION</h3>
    <div class="name">Cutwell &amp; Co</div>
    <a class="btn">Discover more</a>
  </article>
</section>

<section class="pricing">
  <div class="abs eyebrow">Choose package</div>
  <h2 class="abs">Tallomex Services Pricing</h2>
  <p class="abs sub">Affordable pricing when compared with increases in appointments.</p>
  <article class="abs plan" style="left:16px">
    <div class="ico"><svg width="26" height="26" viewBox="0 0 26 26" fill="none" stroke="#fff" stroke-width="2"><path d="M13 4l10 5-10 5-10-5z"/><path d="M3 14l10 5 10-5"/></svg></div>
    <h3>STARTER</h3>
    <p class="desc">Pharetra turpis suscipit primis et enim sodales arcu aliquet integer</p>
    <div class="price">€370<sup>/month</sup></div>
    <ul><li>Dignissim vel augue habitant</li><li>Lobortis enim conubia eget</li><li>Luctus gravida duis tellus leo</li><li>A libero egestas augue</li><li>Nunc pharetra quisque quam</li></ul>
    <a class="btn">Get Started</a>
    <p class="note">*Pulvinar finibus volutpat ipsum consectetuer aliquet fusce mauris fermentum ac</p>
  </article>
  <article class="abs plan featured" style="left:433px">
    <div class="ico"><svg width="26" height="26" viewBox="0 0 26 26" fill="none" stroke="#0094D4" stroke-width="2"><rect x="4" y="3" width="18" height="20"/><path d="M9 18v-5M13 18V9M17 18v-7"/></svg></div>
    <h3>PREMIUM</h3>
    <p class="desc">Pharetra turpis suscipit primis et enim sodales arcu aliquet integer</p>
    <div class="price">$99<sup>/month</sup></div>
    <ul><li>Dignissim vel augue habitant</li><li>Lobortis enim conubia eget</li><li>Luctus gravida duis tellus leo</li><li>A libero egestas augue</li><li>Nunc pharetra quisque quam</li></ul>
    <a class="btn">Get Started</a>
    <p class="note">*Pulvinar finibus volutpat ipsum consectetuer aliquet fusce mauris fermentum ac</p>
  </article>
  <article class="abs plan alt" style="left:795px">
    <div class="ico"><svg width="26" height="26" viewBox="0 0 26 26" fill="none" stroke="#fff" stroke-width="2"><path d="M5 9l4-5h8l4 5-8 13z"/><path d="M5 9h16"/></svg></div>
    <h3>ULTIMATE</h3>
    <p class="desc">Pharetra turpis suscipit primis et enim sodales arcu aliquet integer</p>
    <div class="price">$149<sup>/month</sup></div>
    <ul><li>Dignissim vel augue habitant</li><li>Lobortis enim conubia eget</li><li>Luctus gravida duis tellus leo</li><li>A libero egestas augue</li><li>Nunc pharetra quisque quam</li></ul>
    <a class="btn">Get Started</a>
    <p class="note">*Pulvinar finibus volutpat ipsum consectetuer aliquet fusce mauris fermentum ac</p>
  </article>
</section>

<section class="contact">
  <div class="abs contact-panel">
    <div class="contact-visual" role="img" aria-label="Blue-tinted photo of a person working at a desk"></div>
    <div class="abs eyebrow">Get in touch</div>
    <h2 class="abs">Contact our<br>sales</h2>
    <p class="abs">Justo mauris sit fermentum mus natoque quis lacinia adipiscing tempus.</p>
    <div class="abs mail">info@tallomex-sample.com</div>
    <div class="abs tel">+353 1 555 0142</div>
  </div>
  <div class="abs form-card">
    <h2 class="abs">Free Market Reserach</h2>
    <p class="abs intro">Lorem ipsum dolor sit amet, consectetur adipiscing elit. Ut elit tellus, luctus nec ullamcorper mattis, pulvinar dapibus leo.</p>
    <label style="left:61px;top:165px">Name</label>
    <div class="field" style="left:61px;top:184px;width:257px;height:43px">Name</div>
    <label style="left:328px;top:165px">Email</label>
    <div class="field" style="left:328px;top:184px;width:258px;height:43px">Email</div>
    <label style="left:61px;top:242px">Message</label>
    <div class="field" style="left:61px;top:261px;width:525px;height:94px">Message</div>
    <a class="abs btn">Free a quote</a>
  </div>
</section>

<section class="newsletter">
  <h2 class="abs">Signup our newsletter to get update information,<br>news, insight or promotions.</h2>
  <div class="field">Email</div>
  <a class="abs signup"><svg width="14" height="12" viewBox="0 0 14 12" fill="none" stroke="#fff" stroke-width="1.5"><rect x="1" y="1" width="12" height="10"/><path d="M1 1l6 5 6-5"/></svg>Sign Up</a>
</section>

<footer class="site-footer">
  <div class="abs logo"><i></i>Tallomex</div>
  <div class="abs fcol" style="left:393px">
    <h4>Services</h4>
    <a>Business Strategy</a><a>Financial Planning</a><a>Project Management</a><a>Tax Consulting</a><a>Audit &amp; Evaluation</a><a>Quality Resourcing</a>
  </div>
  <div class="abs fcol" style="left:614px">
    <h4>Company</h4>
    <a>About us</a><a>Leadership</a><a>Careers</a><a>News &amp; Article</a><a>Legal Notice</a>
  </div>
  <div class="abs fcol" style="left:838px;width:320px">
    <h4>Get in touch</h4>
    <p>Northbay Institute of Technology, Kilrane, Co. Wexford Ireland Y35 K2P</p>
    <p style="margin:12px 0 0 24px">info@tallomex-sample.com</p>
    <p style="margin-left:24px">+353 1 555 0142</p>
    <div class="socials"><span></span><span></span><span></span><span></span></div>
  </div>
  <div class="abs legal" style="left:55px">Copyright © 2024, All rights reserved.</div>
  <div class="abs legal" style="left:880px">Term of use &nbsp;•&nbsp; Privacy Policy &nbsp;•&nbsp; Cookie Policy</div>
</footer>

</body>
</html>
```